Need Help having my business card stand out

I am the owner of Birchway Canine Training and would like for my business cards to stand out. I have been trying to keep designing them myself but I can't get what I have in my head on the card. I will try my best to post templates that I like for inspirations. I want something unique but elegant. I don't want in to look cartoony or cheesy. It needs to pop in a pet shop but also in a coffee shop or gym.

Target Market(s)

Dog owners, Married ,No young kids Jr High school kids and up (maybe kids on the way) Executives, Stay at home moms/wives, Small business owners

Industry/Entity Type

Dog Training

Contact Information for Business Card

Lowell Spratt, 281-904-3376, info@birchwaycanine.example, www.birchwaycanine.example

Colors

Designer to choose colors to be used in the design.

Requirements
Must have
• my logo
Should not have
• Cursive lettering

```html
<!DOCTYPE html>
<html lang="en">
<head>
<meta charset="utf-8">
<title>Birchway Canine Training — Business Card</title>
<link rel="stylesheet" href="https://fonts.googleapis.com/css2?family=Kanit:wght@300;400;500&display=swap">
<style>
  :root {
    --page-bg: #e9e6e1;
    --card-dark: #1b1b1b;
    --band-grey: #6b6b6b;
    --ink-light: #ffffff;
    --card-shadow: rgba(0, 0, 0, 0.28);
  }
  * { box-sizing: border-box; margin: 0; padding: 0; }
  html, body {
    width: 1200px;
    height: 994px;
    overflow: hidden;
    background: var(--page-bg);
  }
  .stage {
    width: 1200px;
    height: 994px;
    display: flex;
    align-items: center;
    justify-content: center;
  }
  .card {
    position: relative;
    width: 510px;
    height: 880px;
    background: var(--card-dark);
    color: var(--ink-light);
    font-family: "Kanit", sans-serif;
    box-shadow: 0 14px 40px var(--card-shadow);
    display: flex;
    flex-direction: column;
    align-items: center;
  }
  .brand {
    margin-top: 150px;
    display: flex;
    flex-direction: column;
    align-items: center;
    gap: 22px;
  }
  .brand-mark {
    width: 34px;
    height: 34px;
    border-radius: 50%;
    background: var(--ink-light);
  }
  .brand-name {
    font-weight: 500;
    font-size: 36px;
    line-height: 1.15;
    letter-spacing: 1px;
    text-align: center;
  }
  .owner-name {
    margin-top: 150px;
    font-weight: 500;
    font-size: 38px;
    letter-spacing: 1px;
    text-transform: uppercase;
  }
  .phone {
    margin-top: 24px;
    font-weight: 300;
    font-size: 27px;
    letter-spacing: 0.5px;
  }
  .email {
    margin-top: 40px;
    font-weight: 300;
    font-size: 26px;
    letter-spacing: 0.5px;
  }
  .web-band {
    position: absolute;
    left: 0;
    right: 0;
    bottom: 0;
    height: 160px;
    background: var(--band-grey);
    display: flex;
    align-items: center;
    justify-content: center;
  }
  .website {
    font-weight: 400;
    font-size: 27px;
    letter-spacing: 0.5px;
  }
</style>
</head>
<body>
  <main class="stage">
    <article class="card">
      <header class="brand">
        <span class="brand-mark" aria-hidden="true"></span>
        <h1 class="brand-name">Birchway Canine<br>Training</h1>
      </header>
      <h2 class="owner-name">Lowell Spratt</h2>
      <p class="phone">281-904-3376</p>
      <p class="email">info@birchwaycanine.example</p>
      <footer class="web-band">
        <p class="website">www.birchwaycanine.example</p>
      </footer>
    </article>
  </main>
</body>
</html>
```